LinkedIn Banner Design for B2B Consulting Firm

Take the already developed logo (attached) and incorporate it into a creative banner design for placement on LinkedIn (the social media platform targeting business users). The banner will be used on the firm's company profile page on LinkedIn (not yet created).

```html
<!DOCTYPE html>
<html lang="en">
<head>
<meta charset="utf-8">
<title>LinkedIn Banner Variants</title>
<link rel="stylesheet" href="https://fonts.googleapis.com/css2?family=Lato:wght@700;900&display=swap">
<style>
  :root {
    --board: #dcd9da;
    --banner: #ffffff;
    --brand-green: #3d6649;
    --label-text: #ffffff;
    --shadow: rgba(0, 0, 0, 0.12);
  }
  * { margin: 0; padding: 0; box-sizing: border-box; }
  html, body {
    width: 1200px;
    height: 797px;
    overflow: hidden;
    background: var(--board);
    font-family: "Lato", Arial, sans-serif;
  }
  .board {
    position: relative;
    width: 1200px;
    height: 797px;
  }
  .banner {
    position: absolute;
    left: 81px;
    width: 1037px;
    height: 175px;
    background: var(--banner);
    box-shadow: 0 1px 3px var(--shadow);
    overflow: hidden;
  }
  .banner--one { top: 112px; }
  .banner--two { top: 311px; }
  .banner--three { top: 508px; }

  .service-label {
    position: absolute;
    left: 282px;
    top: 27px;
    width: 295px;
    height: 30px;
    background: var(--brand-green);
    color: var(--label-text);
    font-weight: 700;
    font-size: 16px;
    line-height: 30px;
    text-align: center;
    letter-spacing: -0.1px;
  }
  .audience {
    position: absolute;
    left: 283px;
    top: 66px;
    color: var(--brand-green);
    font-weight: 700;
    font-size: 23px;
    line-height: 27.5px;
    letter-spacing: -0.2px;
  }
  .brand-name {
    position: absolute;
    left: 585px;
    top: 104px;
    display: flex;
    align-items: center;
    gap: 12px;
    color: var(--brand-green);
    font-weight: 700;
    font-size: 30px;
    line-height: 36px;
    white-space: nowrap;
  }
  .brand-name::before {
    content: "";
    width: 28px;
    height: 28px;
    background: var(--brand-green);
  }
  .team-photo {
    position: absolute;
    top: 0;
    left: 0;
    width: 1037px;
    height: 175px;
    clip-path: polygon(651px 0, 1037px 0, 1037px 175px, 828px 175px);
  }
  .team-photo--office {
    background: linear-gradient(100deg, #6e7b86 0%, #b9c6cf 35%, #d7dde2 55%, #8a8f96 80%, #c9ced4 100%);
  }
  .team-photo--studio {
    background: linear-gradient(100deg, #3b3230 0%, #6b5a4c 30%, #c7b07a 50%, #5d4a42 70%, #8d8479 100%);
  }
  .team-photo--loft {
    background: linear-gradient(100deg, #a8553f 0%, #c9a28c 30%, #e3dcd6 50%, #b08a5c 70%, #6d6a6c 100%);
  }
</style>
</head>
<body>
<main class="board">
  <section class="banner banner--one">
    <div class="team-photo team-photo--office" role="img" aria-label="Photo of a diverse business team smiling around a laptop in a bright office"></div>
    <p class="service-label">Fractional&nbsp; Marketing Services</p>
    <h2 class="audience">For Private Equity Firms,<br>Family Offices and<br>Investment Banks</h2>
    <p class="brand-name">Alder Point</p>
  </section>

  <section class="banner banner--two">
    <div class="team-photo team-photo--studio" role="img" aria-label="Photo of a young team gathered around a laptop in a warm office with plants"></div>
    <p class="service-label">Fractional&nbsp; Marketing Services</p>
    <h2 class="audience">For Private Equity Firms,<br>Family Offices and<br>Investment Banks</h2>
    <p class="brand-name">Alder Point</p>
  </section>

  <section class="banner banner--three">
    <div class="team-photo team-photo--loft" role="img" aria-label="Photo of colleagues collaborating at a laptop in a brick-walled loft office"></div>
    <p class="service-label">Fractional&nbsp; Marketing Services</p>
    <h2 class="audience">For Private Equity Firms,<br>Family Offices and<br>Investment Banks</h2>
    <p class="brand-name">Alder Point</p>
  </section>
</main>
</body>
</html>
```